Unique Business Card Design

Unique Business Card design for our orthotic and prosthetic company. Our logo is on our website, color is light blue. Unique shape (artificial leg shaped, vertical, etc..) preferred. Logo, business name, individual name and basic demographics needed.

Industry/Entity Type

Business

Contact Information for Business Card

Logo, Industry, Phone # Logo, "Prosthetic & Orthotic Services" Place to add individual name and contact info

Colors
cee9f5

Requirements
Must have
• The icon must be there, placement of "Prosthetic & Orthotic Services" can be moved
Nice to have
• Like the mix of light blue, and a little darker blue. One design included the icons from my website which was a nice touch

```html
<!DOCTYPE html>
<html lang="en">
<head>
<meta charset="utf-8">
<title>Limbworks Inc. Business Card</title>
<link rel="stylesheet" href="https://fonts.googleapis.com/css2?family=Roboto:wght@400;500;700&family=Crimson+Text:ital@1&display=swap">
<style>
  :root {
    --bg: #e9ebee;
    --blue-deep: #0a5aaa;
    --blue-mid: #1a9be2;
    --blue-ink: #1b5ea9;
    --brand: #0d5aa7;
    --white: #ffffff;
    --grey-text: #5c5f63;
    --faint: #f2f5f9;
    --divider: #d4d7db;
    --bubble: #bcd8f5;
  }
  * { margin: 0; padding: 0; box-sizing: border-box; }
  html, body { width: 1200px; height: 1000px; overflow: hidden; }
  body {
    background: var(--bg);
    font-family: "Roboto", Arial, sans-serif;
    position: relative;
  }
  .card {
    position: absolute;
    left: 220px;
    width: 760px;
    border-radius: 28px;
    overflow: hidden;
    box-shadow: 0 6px 18px rgba(0,0,0,.22);
  }
  .card--front {
    top: 50px;
    height: 433px;
    background: linear-gradient(90deg, var(--blue-deep) 0%, var(--blue-mid) 45%, var(--blue-mid) 60%, var(--blue-deep) 100%);
    color: var(--white);
  }
  .card--back {
    top: 524px;
    height: 436px;
    background: var(--white);
  }
  .abs { position: absolute; }
  .brand-dot { border-radius: 50%; }
  .front-dot { left: 138px; top: 110px; width: 132px; height: 132px; background: var(--white); }
  .brand-name {
    font-weight: 500;
    white-space: nowrap;
    letter-spacing: .3px;
  }
  .front-name { left: 285px; top: 128px; font-size: 40px; color: var(--white); }
  .tagline {
    font-family: "Crimson Text", Georgia, serif;
    font-style: italic;
    white-space: nowrap;
  }
  .front-tagline { left: 307px; top: 184px; font-size: 23px; color: var(--white); }
  .service { width: 130px; text-align: center; top: 310px; }
  .service__icon {
    width: 58px; height: 58px; border-radius: 50%;
    margin: 0 auto;
    background: radial-gradient(circle at 40% 35%, #eef6ff 0%, var(--bubble) 60%, #8fbbe8 100%);
    border: 2px solid rgba(255,255,255,.55);
  }
  .service__label { margin-top: 14px; font-size: 15px; font-weight: 500; letter-spacing: .3px; }
  .s1 { left: 188px; } .s2 { left: 320px; } .s3 { left: 444px; }

  .faint-disc { left: 48px; top: 46px; width: 344px; height: 344px; border-radius: 50%; background: var(--faint); }
  .back-dot { left: 43px; top: 170px; width: 96px; height: 96px; background: var(--brand); }
  .back-name { left: 150px; top: 180px; font-size: 29px; color: var(--brand); }
  .back-tagline { left: 166px; top: 224px; font-size: 17px; color: var(--brand); }
  .divider { left: 418px; top: 94px; width: 1px; height: 246px; background: var(--divider); }
  .contact { left: 442px; top: 88px; color: var(--grey-text); font-size: 16.5px; line-height: 23.5px; }
  .contact__name { font-size: 23px; font-weight: 700; color: var(--blue-ink); line-height: 28px; }
  .contact__title { margin-bottom: 14px; }
  .contact__company { color: var(--blue-ink); }
  .contact__list { margin-top: 8px; list-style: none; line-height: 24.5px; }
  .contact__list li { display: flex; align-items: center; gap: 6px; }
  .contact__list svg { width: 14px; height: 14px; fill: var(--blue-ink); flex: none; }
  .web-main { color: var(--blue-ink); }
  .bottom-rule { left: 0; top: 412px; width: 100%; height: 3px; background: var(--divider); }
  .bottom-band { left: 0; top: 418px; width: 100%; height: 18px; background: linear-gradient(90deg, var(--blue-deep), var(--blue-mid) 50%, var(--blue-deep)); }
</style>
</head>
<body>
  <section class="card card--front">
    <div class="abs brand-dot front-dot"></div>
    <div class="abs brand-name front-name">LIMBWORKS INC.</div>
    <div class="abs tagline front-tagline">Prosthetic &amp; Orthotic Services</div>

    <div class="abs service s1">
      <div class="service__icon" role="img" aria-label="Knee joint icon"></div>
      <div class="service__label">Orthotics</div>
    </div>
    <div class="abs service s2">
      <div class="service__icon" role="img" aria-label="Standing person icon"></div>
      <div class="service__label">Prosthetics</div>
    </div>
    <div class="abs service s3">
      <div class="service__icon" role="img" aria-label="Wheelchair icon"></div>
      <div class="service__label">Vascular</div>
    </div>
  </section>

  <section class="card card--back">
    <div class="abs faint-disc"></div>
    <div class="abs brand-dot back-dot"></div>
    <div class="abs brand-name back-name">LIMBWORKS INC.</div>
    <div class="abs tagline back-tagline">Prosthetic &amp; Orthotic Services</div>

    <div class="abs divider"></div>

    <div class="abs contact">
      <div class="contact__name">Miriam Castell</div>
      <div class="contact__title">CO LPO</div>
      <div class="contact__company">LIMBWORKS INC.</div>
      <div>1450 West 14th Street</div>
      <div>Riverton, NY 11890</div>
      <ul class="contact__list">
        <li><svg viewBox="0 0 14 14"><path d="M4 0h6a1 1 0 0 1 1 1v12a1 1 0 0 1-1 1H4a1 1 0 0 1-1-1V1a1 1 0 0 1 1-1zm.5 1.5v9h5v-9zM7 11.5a.8.8 0 1 0 0 1.6.8.8 0 0 0 0-1.6z"/></svg>845-5550142</li>
        <li><svg viewBox="0 0 14 14"><path d="M3 1l2.2 2.6-1.2 1.6c.8 1.8 2.2 3.2 4 4l1.6-1.2L12 10.2 10.6 12C5.8 11.6 2.4 8.2 2 3.4z"/></svg>(718) 555-0170</li>
        <li><svg viewBox="0 0 14 14"><path d="M3.5 1h7v3h-7zM1 5h12v5h-2v3H3v-3H1zm3.5 3.5V12h5V8.5z"/></svg>(718) 555-0139</li>
        <li><svg viewBox="0 0 14 14"><path d="M1 3h12v8H1zm1 1v.3l5 3.4 5-3.4V4z"/></svg>mcastell@limbworksinc.com</li>
        <li><svg viewBox="0 0 14 14"><path d="M7 1a6 6 0 1 0 0 12A6 6 0 0 0 7 1zm-.6 1.4v2.2H4.5c.4-1.1 1.1-1.9 1.9-2.2zm1.2 0c.8.3 1.5 1.1 1.9 2.2H7.6zM3.3 4.6h-.9A4.8 4.8 0 0 1 4.3 2.8c-.4.5-.7 1.1-1 1.8zm7.4 0c-.3-.7-.6-1.3-1-1.8a4.8 4.8 0 0 1 1.9 1.8zM2.2 5.8h1.2a9 9 0 0 0 0 2.4H2.2a4.8 4.8 0 0 1 0-2.4zm2.4 0h1.8v2.4H4.6a8 8 0 0 1 0-2.4zm3 0h1.8a8 8 0 0 1 0 2.4H7.6zm3 0h1.2a4.8 4.8 0 0 1 0 2.4h-1.2a9 9 0 0 0 0-2.4zM2.4 9.4h.9c.3.7.6 1.3 1 1.8a4.8 4.8 0 0 1-1.9-1.8zm2.1 0h1.9v2.2c-.8-.3-1.5-1.1-1.9-2.2zm3.1 0h1.9c-.4 1.1-1.1 1.9-1.9 2.2zm3.1 0h.9a4.8 4.8 0 0 1-1.9 1.8c.4-.5.7-1.1 1-1.8z"/></svg><span>www.<span class="web-main">limbworksinc</span>.net</span></li>
      </ul>
    </div>

    <div class="abs bottom-rule"></div>
    <div class="abs bottom-band"></div>
  </section>
</body>
</html>
```